Building company buisness cards

We are looking for a sharp modern new look for our business cards.
We are a New Zealand based company that specialises in house and land packages.
We have attached a photo of the current logo and would like to see if it can be improved somehow if needed.
We are open to any colours but we have chosen green at this stage.
Feel free to change the font and make the logo smarter looking.
Play with the colours and see what looks best.

We want a card that looks so good know one will want to throw it away!

Target Market(s)

Home buyers

Industry/Entity Type

Building

Contact Information for Business Card

Derek Tolvane
0217394062
dtolvane@quillmarkhomesteads.co.nz
quillmarkhomesteads.co.nz

Font styles to use
Serif
Sans Serif

Colors

Designer to choose colors to be used in the design.

Requirements
Must have
• Logo and company name on one side, details on the other side
Nice to have
• Color codes for the original green are HEX #4a8028, RGB(74,128,40), CMYK(42,0,69,50)
• Round corners, Raised and/or spot UV

```html
<!DOCTYPE html>
<html lang="en">
<head>
<meta charset="utf-8">
<title>Quillmark Homesteads – Business Cards</title>
<link rel="stylesheet" href="https://fonts.googleapis.com/css2?family=Poppins:wght@700&family=Open+Sans:wght@300;400&display=swap">
<style>
  :root {
    --brand-green: #4a8028;
    --brand-green-dark: #3f6e32;
    --pattern-green: #4d7f3f;
    --card-white: #fbfbfb;
    --faint-grey: #e6e8e4;
    --ink: #1e1e1e;
    --backdrop: #ecebe7;
  }
  * { margin: 0; padding: 0; box-sizing: border-box; }
  html, body { width: 1200px; height: 1021px; overflow: hidden; }
  body {
    background: var(--backdrop);
    display: flex;
    flex-direction: column;
    align-items: center;
    justify-content: center;
    gap: 34px;
    font-family: "Open Sans", sans-serif;
  }
  .card {
    position: relative;
    width: 760px;
    height: 464px;
    border-radius: 26px;
    overflow: hidden;
    box-shadow: 0 6px 18px rgba(0,0,0,0.12);
  }
  /* front: logo side */
  .card--front { background: var(--brand-green-dark); }
  .front-pattern {
    position: absolute; inset: 0;
    background: linear-gradient(135deg, #5a8c4c 0%, var(--pattern-green) 45%, #3b6a2f 100%);
  }
  .front-brand {
    position: absolute; left: 0; right: 0; top: 50%;
    transform: translateY(-50%);
    display: flex; align-items: center; justify-content: center; gap: 16px;
  }
  .brand-mark {
    width: 22px; height: 22px;
    background: #ffffff;
    flex: none;
  }
  .brand-name {
    font-family: "Poppins", sans-serif;
    font-weight: 700;
    font-size: 46px;
    letter-spacing: 0.5px;
    color: #ffffff;
    line-height: 1;
  }
  /* back: details side */
  .card--back { background: var(--card-white); }
  .back-decoration {
    position: absolute; left: 70px; top: 0;
    width: 330px; height: 464px;
    background: linear-gradient(180deg, var(--faint-grey) 0%, rgba(230,232,228,0.4) 100%);
    opacity: 0.7;
  }
  .name-band {
    position: absolute; left: 0; top: 230px;
    width: 392px; height: 100px;
    background: var(--brand-green);
    padding: 16px 0 0 66px;
    color: #ffffff;
  }
  .person-name {
    font-family: "Poppins", sans-serif;
    font-weight: 700;
    font-size: 27px;
    line-height: 1.15;
  }
  .person-role {
    font-weight: 300;
    font-size: 19px;
    line-height: 1.2;
  }
  .back-brand {
    position: absolute; right: 60px; top: 90px;
    display: flex; align-items: center; gap: 14px;
  }
  .back-brand .brand-mark { background: var(--brand-green); }
  .back-brand .brand-name { color: var(--brand-green); font-size: 44px; line-height: 1.05; }
  .contact-list {
    position: absolute; right: 48px; top: 352px;
    list-style: none;
    color: var(--ink);
    font-size: 19px;
    line-height: 1.5;
  }
  .contact-list li { display: flex; justify-content: flex-end; align-items: center; gap: 10px; }
  .contact-icon { width: 18px; height: 18px; flex: none; }
</style>
</head>
<body>

  <section class="card card--front">
    <div class="front-pattern" role="img" aria-label="Embossed repeating pattern of small house icons in darker green"></div>
    <div class="front-brand">
      <span class="brand-mark"></span>
      <span class="brand-name">quillmark homesteads</span>
    </div>
  </section>

  <section class="card card--back">
    <div class="back-decoration" role="img" aria-label="Large faint illustration of a house roof sheltering a family"></div>

    <div class="name-band">
      <p class="person-name">Derek Tolvane</p>
      <p class="person-role">Founder</p>
    </div>

    <div class="back-brand">
      <span class="brand-mark"></span>
      <span class="brand-name">quillmark<br>homesteads</span>
    </div>

    <ul class="contact-list">
      <li>0217394062
        <svg class="contact-icon" viewBox="0 0 24 24" aria-hidden="true"><path fill="#4a8028" d="M6.6 10.8a15.1 15.1 0 0 0 6.6 6.6l2.2-2.2c.3-.3.7-.4 1-.2 1.1.4 2.3.6 3.6.6.6 0 1 .4 1 1V20c0 .6-.4 1-1 1A17 17 0 0 1 3 4c0-.6.4-1 1-1h3.5c.6 0 1 .4 1 1 0 1.3.2 2.5.6 3.6.1.3 0 .7-.2 1z"/></svg>
      </li>
      <li>dtolvane@quillmarkhomesteads.co.nz
        <svg class="contact-icon" viewBox="0 0 24 24" aria-hidden="true"><rect x="2.5" y="5" width="19" height="14" rx="1.5" fill="none" stroke="#4a8028" stroke-width="2"/><path d="M3 6l9 7 9-7" fill="none" stroke="#4a8028" stroke-width="2"/></svg>
      </li>
      <li>quillmarkhomesteads.co.nz
        <svg class="contact-icon" viewBox="0 0 24 24" aria-hidden="true"><g fill="none" stroke="#4a8028" stroke-width="1.8"><circle cx="12" cy="12" r="9.5"/><ellipse cx="12" cy="12" rx="4.5" ry="9.5"/><path d="M2.5 12h19M4 7h16M4 17h16"/></g></svg>
      </li>
    </ul>
  </section>

</body>
</html>
```